Website for a Psychologist in Private Practice

I need a cool web design for my website: www.drkalvoric.com. I would like it to look professional. Keep all the current content and add: Space for video; radio spots (see Silver Cedar Tunes Logo below for those); Quick Inquiry; Friendora link; 5 star rating on Rivo; a map; reviews from former patients. I am open to suggestions.

Target Market(s)

Those seeking individual and marital counseling.

Industry/Entity Type

Mental Health

Number of Pages Required

1 page

Font styles to use
Sans Serif
Other font styles liked:
• I'm open but no hard to read script

Requirements
Must have
• All the content on my home page with link for video and radio spots. List services and degrees and expertices (pics not necessary).
Nice to have
• A video of me and radio conversations (logo of Silver Cedar Tunes radio attached).
Should not have
• Cartoons, comedy, etc.... I don't need pictures of services (marital, depression, etc...) Just list those.

```html
<!DOCTYPE html>
<html lang="en">
<head>
<meta charset="utf-8">
<title>Dr. Dana Z. Kalvoric – Psychologist</title>
<link href="https://fonts.googleapis.com/css2?family=Barlow:wght@400;500;600&family=Arimo:ital,wght@0,400;0,700;1,400;1,700&display=swap" rel="stylesheet">
<style>
:root{
  --blue:#2a7ec3;
  --blue-dark:#1f6aa8;
  --ink:#333;
  --white:#fff;
  --footer:#2b2a29;
  --panel:rgba(20,45,60,.35);
  --band:rgba(10,45,45,.7);
  --reviews:rgba(70,58,45,.78);
  --field:rgba(60,60,60,.55);
}
*{margin:0;padding:0;box-sizing:border-box}
html,body{width:743px;height:1200px;overflow:hidden}
body{position:relative;font-family:"Arimo",sans-serif;color:var(--ink);background:#fff}
.abs{position:absolute}
.head{font-family:"Barlow",sans-serif}
/* header */
.top-rule{left:0;top:0;width:743px;height:2px;background:var(--blue)}
.brand{left:83px;top:16px;font-family:"Barlow",sans-serif;font-weight:500;font-size:24px;color:var(--blue)}
.license{left:445px;top:33px;font-size:8.5px;color:#222}
.call{left:553px;top:17px}
.call-label{left:576px;top:19px;font-size:9.5px;color:#222}
.call-number{left:578px;top:30px;font-family:"Barlow",sans-serif;font-size:15px;color:var(--blue)}
/* nav */
.nav{left:0;top:58px;width:743px;height:28px;background:var(--blue)}
.nav a{position:absolute;top:0;height:28px;line-height:28px;font-family:"Barlow",sans-serif;font-size:10.5px;color:#fff;text-decoration:none}
.nav .sep{position:absolute;top:0;width:1px;height:28px;background:rgba(0,0,0,.15)}
.nav .current{color:#111;font-weight:600}
.follow{left:558px;top:0;font-size:8px;color:#fff;line-height:28px}
.social{top:5px;height:18px;line-height:18px;font-size:7px;color:#fff;padding:0 5px;border-radius:9px;background:var(--blue-dark)}
/* hero */
.hero{left:0;top:86px;width:743px;height:272px;background:linear-gradient(180deg,#8fa9b8 0%,#d8c99a 40%,#f0dc9a 55%,#a9b46a 72%,#6f8d2e 100%)}
.hero-title{left:82px;top:167px;font-family:"Barlow",sans-serif;font-weight:500;font-size:17px;color:var(--blue)}
.hero-text{left:82px;top:193px;width:200px;font-family:"Barlow",sans-serif;font-weight:500;font-size:14.5px;line-height:21.5px;color:#2f2f2f}
.arrow{top:212px;width:22px;height:20px;background:#3a3a3a;border:1px solid #fff}
/* content */
.beach{left:0;top:358px;width:743px;height:664px;background:linear-gradient(180deg,#6aa3c7 0%,#47b2c0 25%,#2f8f9c 50%,#a29480 78%,#c7b08e 100%)}
.panel{left:82px;top:358px;width:581px;height:222px;background:var(--panel)}
.panel2{left:82px;top:628px;width:581px;height:214px;background:rgba(40,60,60,.35)}
.col-title{font-family:"Barlow",sans-serif;font-weight:500;font-size:14px;line-height:15px;color:#fff}
.rule{height:2px;background:var(--blue)}
.rule::before{content:"";position:absolute;left:0;top:0;width:60px;height:2px;background:#111}
.about-text{left:88px;top:427px;width:172px;font-size:8.2px;line-height:13px;color:#fff}
.about-text a,.link{color:#fff;text-decoration:underline}
.photo{border-radius:50%;border:2px solid #fff;background:linear-gradient(160deg,#e3c98d,#8a7c6a 70%,#4a6a8c)}
.expert-name{left:357px;top:440px;font-family:"Barlow",sans-serif;font-weight:500;font-size:13.5px;line-height:17px;color:#fff}
.expert-list{left:290px;top:488px;list-style:none;font-size:8.3px;line-height:13px;color:#fff}
.expert-list li{padding-left:12px;position:relative}
.expert-list svg{position:absolute;left:0;top:3px}
.quote-box{left:481px;top:428px;width:176px;height:106px;background:rgba(225,228,230,.8);border:1px solid rgba(255,255,255,.6);padding:6px 8px 0 10px}
.quote-box p{font-size:8.2px;line-height:13px;color:#555;text-indent:12px}
.quote-box .by{font-family:serif;font-size:8px;text-align:right;margin-top:3px;color:#555}
.vsep{left:272px;top:380px;width:1px;height:172px;background:rgba(255,255,255,.4)}
/* degrees */
.degrees{left:82px;top:580px;width:581px;height:48px;background:var(--band)}
.degrees-title{left:147px;top:595px;font-family:"Barlow",sans-serif;font-weight:500;font-size:14px;color:#fff}
.degree{font-size:8.5px;color:#fff}
/* video, inquiry */
.video{left:88px;top:678px;width:181px;height:137px;border:2px solid var(--blue);background:linear-gradient(160deg,#e8d6a8,#9c8a72 55%,#3f5e82)}
.play{left:160px;top:737px}
.inq-note{left:293px;top:681px;font-size:7.2px;color:#fff}
.field{left:293px;width:172px;height:19px;background:var(--field);font-size:7.2px;color:#ddd;padding:6px 6px 0}
.submit{left:293px;top:797px;width:68px;height:19px;background:var(--blue);color:#fff;font-family:"Barlow",sans-serif;font-weight:600;font-size:9.5px;text-align:center;line-height:19px}
.poster{left:486px;top:652px;width:163px;height:163px;background:linear-gradient(180deg,#e23d63 0%,#b0485e 30%,#6a4f45 70%,#c7a07a 100%)}
/* reviews */
.reviews{left:82px;top:842px;width:581px;height:180px;background:var(--reviews)}
.rev-title{left:0;top:859px;width:743px;text-align:center;font-family:"Barlow",sans-serif;font-weight:500;font-size:14px;color:#fff}
.rev-text{left:195px;top:902px;width:452px;font-style:italic;font-size:8.2px;line-height:14.6px;color:#fff}
.rev-by{left:173px;top:969px;font-style:italic;font-weight:700;font-size:8px;color:#fff}
.rev-more{left:563px;top:982px;font-size:8px;color:#fff}
/* footer */
.footer{left:0;top:1022px;width:743px;height:152px;background:var(--footer)}
.f-title{top:1038px;font-size:9px;color:#fff}
.f-dots{top:1053px;border-top:1px dashed #777}
.f-links{left:88px;top:1062px;list-style:none;font-size:8px;line-height:13.6px;color:#fff}
.f-links .on{color:#d98a3a}
.badge{left:212px;width:127px;border:2px solid #3a8ac9}
.contact{font-size:8px;color:#fff}
.rivo{left:594px;top:1059px;width:52px;height:50px;border-radius:8px;background:#c8242b;border:2px solid #eee;display:flex;align-items:center;justify-content:center;font-family:"Barlow",sans-serif;font-weight:600;font-size:11px;color:#fff}
.share{left:591px;top:1120px;width:58px;height:18px;background:#3d5f9a;border:1px solid #7a93bf;font-size:7.5px;color:#fff;display:flex;align-items:center;gap:5px;padding-left:5px}
.share i{display:block;width:9px;height:9px;background:#fff}
.copy{left:0;top:1174px;width:743px;height:26px;background:var(--blue);text-align:center;line-height:26px;font-size:8px;color:#fff}
</style>
</head>
<body>
<div class="abs top-rule"></div>
<header>
  <div class="abs brand">Dr. Dana Z. Kalvoric</div>
  <div class="abs license">California # PSY10482</div>
  <svg class="abs call" width="20" height="20" viewBox="0 0 20 20" aria-hidden="true"><circle cx="10" cy="10" r="8.5" fill="none" stroke="#2a7ec3" stroke-width="1.5"/><path d="M7 5.5c-1.5 2.5-1 6.5 2 9l1.6-1.6-1.7-2 .8-2.2L11 7z" fill="#2a7ec3"/></svg>
  <div class="abs call-label">Call Us Today</div>
  <div class="abs call-number">555-014-7726</div>
</header>
<nav class="abs nav">
  <a class="current" style="left:88px">Home</a>
  <span class="sep" style="left:124px"></span>
  <a style="left:135px">About Me</a>
  <span class="sep" style="left:187px"></span>
  <a style="left:198px">Sessions</a>
  <span class="sep" style="left:249px"></span>
  <a style="left:260px">Resources</a>
  <span class="sep" style="left:317px"></span>
  <a style="left:328px">BIO</a>
  <span class="sep" style="left:354px"></span>
  <a style="left:365px">Customer Reviews</a>
  <span class="sep" style="left:458px"></span>
  <a style="left:471px">Contact Us</a>
  <span class="abs follow">Follow Us On</span>
  <span class="abs social" style="left:612px">Friendora</span>
  <span class="abs social" style="left:660px">Chirply</span>
</nav>
<section>
  <div class="abs hero" role="img" aria-label="Man with raised arms in a green field under a sunlit sky"></div>
  <h1 class="abs hero-title">DO NOT COMPROMISE</h1>
  <p class="abs hero-text">Experience separates good psychologists from others with fewer and more proficient sessions</p>
  <div class="abs arrow" style="left:4px"><svg width="20" height="18" viewBox="0 0 20 18"><path d="M12 5l-4 4 4 4" fill="none" stroke="#fff" stroke-width="2"/></svg></div>
  <div class="abs arrow" style="left:713px"><svg width="20" height="18" viewBox="0 0 20 18"><path d="M8 5l4 4-4 4" fill="none" stroke="#fff" stroke-width="2"/></svg></div>
</section>

<main>
  <div class="abs beach" role="img" aria-label="Tropical beach with turquoise water and sand"></div>
  <div class="abs panel"></div>
  <div class="abs panel2"></div>
  <div class="abs vsep"></div>

  <h2 class="abs col-title" style="left:90px;top:381px">About<br>Dr. Dana Z. Kalvoric</h2>
  <div class="abs rule" style="left:88px;top:415px;width:173px"></div>
  <p class="abs about-text">While I acknowledge the importance of my education, I also appreciate the role my experiences have played in allowing me to relate so well to others. Allow me to share those I feel are most relevant with you.<br>I survived an abusive childhood that my mother &amp; sister unfortunately did not. &amp; it was my grief &amp; desire to become stronger than my past that led me to counseling.....<br><a href="#">Read More</a></p>

  <h2 class="abs col-title" style="left:288px;top:381px">My<br>Expertise</h2>
  <div class="abs rule" style="left:288px;top:415px;width:173px"></div>
  <div class="abs photo" style="left:285px;top:423px;width:64px;height:64px" role="img" aria-label="Portrait of the psychologist"></div>
  <div class="abs expert-name">Dr. Dana Z.<br>Kalvoric</div>
  <ul class="abs expert-list">
    <li><svg width="9" height="8" viewBox="0 0 9 8"><path d="M1 4l2.5 3L8 1" fill="none" stroke="#fff" stroke-width="1.6"/></svg>Dating, Marriage,</li>
    <li><svg width="9" height="8" viewBox="0 0 9 8"><path d="M1 4l2.5 3L8 1" fill="none" stroke="#fff" stroke-width="1.6"/></svg>Parenting &amp; Professional Relationships</li>
    <li><svg width="9" height="8" viewBox="0 0 9 8"><path d="M1 4l2.5 3L8 1" fill="none" stroke="#fff" stroke-width="1.6"/></svg>Depression &amp; Anxiety Issues</li>
    <li><svg width="9" height="8" viewBox="0 0 9 8"><path d="M1 4l2.5 3L8 1" fill="none" stroke="#fff" stroke-width="1.6"/></svg>Personality Disorders</li>
    <li><svg width="9" height="8" viewBox="0 0 9 8"><path d="M1 4l2.5 3L8 1" fill="none" stroke="#fff" stroke-width="1.6"/></svg>Life Management</li>
  </ul>

  <h2 class="abs col-title" style="left:481px;top:381px">Radio<br>Conversations</h2>
  <div class="abs rule" style="left:481px;top:415px;width:173px"></div>
  <div class="abs quote-box">
    <p>Lorem ipsum dolor sit ae onsectetuer adipiscing elit, sed diam nonummy nibh euis tincidunt ut laoreetlore gna aliquam erat olutpat. Ut wisi enim adinim veniam, quis strud xerci tation ullamrper suscipit lobortis sl ut al lorem.</p>
    <div class="by">Joan Sorel</div>
  </div>
  <a class="abs link" style="left:481px;top:540px;font-size:9px" href="#">View All</a>

  <div class="abs degrees"></div>
  <h2 class="abs degrees-title">My Degrees</h2>
  <svg class="abs" style="left:228px;top:588px" width="12" height="34" viewBox="0 0 12 34"><path d="M2 1c6 0 4 14 9 16-5 2-3 16-9 16" fill="none" stroke="#aaa" stroke-width="1.5"/></svg>
  <div class="abs degree" style="left:252px;top:591px">Doctoral Degree in Clinical Psychology</div>
  <div class="abs degree" style="left:252px;top:608px">Masters Degree in Counseling Psychology</div>
  <div class="abs degree" style="left:442px;top:591px">Doctoral Internship, Eastbay Medical Center</div>
  <div class="abs degree" style="left:442px;top:608px">Masters Internship, Marlow Clinic</div>

  <h2 class="abs col-title" style="left:88px;top:650px">View Video</h2>
  <div class="abs rule" style="left:88px;top:668px;width:181px"></div>
  <div class="abs video" role="img" aria-label="Video still of the psychologist"></div>
  <svg class="abs play" width="19" height="19" viewBox="0 0 19 19"><circle cx="9.5" cy="9.5" r="8.5" fill="none" stroke="#fff" stroke-width="1.5"/><path d="M7.5 5.5l5 4-5 4z" fill="#fff"/></svg>

  <h2 class="abs col-title" style="left:292px;top:650px">Quick Inquiry</h2>
  <div class="abs rule" style="left:292px;top:668px;width:173px"></div>
  <p class="abs inq-note">Lorem ipsum dolor sit amet, consectetuer</p>
  <div class="abs field" style="top:696px">Name</div>
  <div class="abs field" style="top:718px">Email</div>
  <div class="abs field" style="top:740px">Phone</div>
  <div class="abs field" style="top:761px;height:32px">Message</div>
  <div class="abs submit">SUBMIT</div>

  <div class="abs poster" role="img" aria-label="Silver Cedar Tunes radio show poster with the hosts and the psychologist"></div>

  <div class="abs reviews"></div>
  <h2 class="abs rev-title">Reviews From Former Patients</h2>
  <div class="abs" style="left:277px;top:882px;width:189px;height:1px;background:#fff"></div>
  <div class="abs" style="left:349px;top:881px;width:45px;height:2px;background:var(--blue)"></div>
  <div class="abs photo" style="left:88px;top:898px;width:72px;height:72px;background:linear-gradient(160deg,#e0e6ea,#b59577 50%,#253a52)" role="img" aria-label="Portrait of a former patient"></div>
  <svg class="abs" style="left:172px;top:900px" width="18" height="14" viewBox="0 0 18 14"><path d="M1 13l4-12h3L5 13zM9 13l4-12h3l-3 12z" fill="#8a7b6c"/></svg>
  <p class="abs rev-text">Lorem ipsum dolor sit amet, consectetuer adipiscing elit, sed diam nonummy nibh euismod tincidunt ut laoreet dolore magna aliquam erat volutpat. Ut wisi enim ad minim veniam, quis nostrud exerci tation ullamcorper suscipit lobortis nisl ut aliquip commodo consequat. Duis autem vel eum iriure dolor in hendrerit in vulputate velit esse molestie consequat, vel illum dolore eu feugiat nulla facilisis at vero eros et accumsan et iusto odio dignissimaugue duis dolore te feugait nulla facilisi.</p>
  <p class="abs rev-by">.... Lorem Ispum, Manger</p>
  <p class="abs rev-more"><a class="link" href="#">Read more testimonials</a> »</p>
</main>

<footer>
  <div class="abs footer"></div>
  <h3 class="abs f-title" style="left:88px">Quick Links</h3>
  <div class="abs f-dots" style="left:88px;width:72px"></div>
  <ul class="abs f-links">
    <li class="on">Home</li><li>About Me</li><li>Sessions</li><li>Resources</li><li>BIO</li><li>Customer Reviews</li><li>Contact Me</li>
  </ul>
  <h3 class="abs f-title" style="left:212px">A Portion of All Revenue Is Donated To</h3>
  <div class="abs f-dots" style="left:212px;width:156px"></div>
  <div class="abs badge" style="top:1061px;height:49px;background:#fff" role="img" aria-label="Children's advocacy partner badge"></div>
  <div class="abs badge" style="top:1114px;height:48px;background:#8aa63e" role="img" aria-label="Family services partner badge"></div>
  <h3 class="abs f-title" style="left:423px">Contact Details</h3>
  <div class="abs f-dots" style="left:423px;width:117px"></div>
  <div class="abs contact" style="left:423px;top:1066px;font-weight:700">A:</div>
  <div class="abs contact" style="left:441px;top:1066px;line-height:12px">418 Larkspur Way, Suite 210<br>Harbor Vale, CA 90000</div>
  <div class="abs contact" style="left:423px;top:1100px;font-weight:700">P:</div>
  <div class="abs contact" style="left:440px;top:1100px">555-014-7726</div>
  <div class="abs contact" style="left:423px;top:1121px;font-weight:700">TF:</div>
  <div class="abs contact" style="left:442px;top:1121px">555-014-7726</div>
  <div class="abs contact" style="left:423px;top:1142px;font-weight:700">E:</div>
  <div class="abs contact" style="left:441px;top:1142px">dk@drkalvoric.com</div>
  <div class="abs rivo">Rivo</div>
  <div class="abs share"><i></i>SHARE</div>
  <div class="abs copy">Copyright © 2016 Dr. Dana Z. Kalvoric&nbsp; All rights reserved</div>
</footer>
</body>
</html>
```